Business Card and Letterhead for Pimlu - modern real estate business

I need a double sided business card design for Pimlu. Please see business card brief here https://files.trelvonadocs.com/sheet/r/7QzTmWbaXLJnoPEd-kRyUgFhHsstbvCe2qfoMxDa_pz/view?mode=shared

Please feel free to design the business cards however you feel best. I am happy to give some creative freedoms and then provide feedback from there.

Please then also create a letterhead to match the business card design

Colors

Designer to choose colors to be used in the design.

Requirements
Must have
• Must be a modern, elegant business card which looks very professional

```html
<!DOCTYPE html>
<html lang="en">
<head>
<meta charset="utf-8">
<title>Pimlu Business Card</title>
<link rel="stylesheet" href="https://fonts.googleapis.com/css2?family=Michroma&family=Montserrat:wght@400;500&display=swap">
<style>
  :root {
    --backdrop: #3a302c;
    --card: #2e2e30;
    --card-edge: #e3141e;
    --accent: #e3141e;
    --ink: #ffffff;
    --ink-soft: #e9e9e9;
    --photo-light: #4a4a4d;
    --photo-dark: #242426;
  }
  * { box-sizing: border-box; margin: 0; padding: 0; }
  html, body {
    width: 1200px;
    height: 800px;
    overflow: hidden;
    background: var(--backdrop);
  }
  .canvas {
    position: relative;
    width: 1200px;
    height: 800px;
    display: flex;
    align-items: center;
    justify-content: center;
    gap: 40px;
  }
  .card {
    position: relative;
    width: 540px;
    height: 310px;
    background: var(--card);
    border: 2px solid var(--card-edge);
    overflow: hidden;
    box-shadow: 0 10px 24px rgba(0,0,0,0.35);
  }
  .card-front {
    display: flex;
    align-items: center;
    justify-content: center;
  }
  .brand-name {
    font-family: "Michroma", sans-serif;
    font-size: 62px;
    letter-spacing: 4px;
    color: var(--accent);
  }
  .card-back .details {
    position: absolute;
    left: 40px;
    top: 40px;
  }
  .agent-name {
    font-family: "Michroma", sans-serif;
    font-size: 17px;
    letter-spacing: 1px;
    color: var(--accent);
    text-transform: uppercase;
  }
  .agent-role {
    font-family: "Montserrat", sans-serif;
    font-size: 13px;
    color: var(--ink);
    margin-top: 3px;
  }
  .rule {
    width: 66px;
    height: 1px;
    background: var(--accent);
    margin: 16px 0 12px;
  }
  .contact-list {
    list-style: none;
    font-family: "Montserrat", sans-serif;
    font-size: 13px;
    color: var(--ink-soft);
  }
  .contact-list li {
    display: flex;
    align-items: center;
    gap: 7px;
    line-height: 19px;
  }
  .contact-list svg { width: 10px; height: 10px; flex: none; }
  .address {
    font-family: "Montserrat", sans-serif;
    font-size: 13px;
    line-height: 19px;
    color: var(--ink-soft);
    font-style: normal;
  }
  .portrait {
    position: absolute;
    right: 28px;
    bottom: 0;
    width: 230px;
    height: 220px;
    background: linear-gradient(180deg, var(--photo-light) 0%, var(--photo-dark) 100%);
    border-radius: 110px 110px 0 0;
  }
</style>
</head>
<body>
<main class="canvas">
  <section class="card card-front" aria-label="Business card front">
    <span class="brand-name">PIMLU</span>
  </section>

  <section class="card card-back" aria-label="Business card back">
    <div class="details">
      <h1 class="agent-name">Liam Carter</h1>
      <p class="agent-role">Licenced Real Estate Agent</p>
      <div class="rule"></div>
      <ul class="contact-list">
        <li>
          <svg viewBox="0 0 10 10"><path fill="#e3141e" d="M2 0.5 L3.6 2.6 L2.7 3.6 Q3.8 5.9 6.3 7.3 L7.4 6.4 L9.5 8 L8.6 9.5 Q4.6 9.3 1.8 6.5 Q0 4 0.5 1.4 Z"/></svg>
          0412 583 906
        </li>
        <li>
          <svg viewBox="0 0 10 10"><rect x="0.5" y="2" width="9" height="6.5" fill="#e3141e"/><path d="M0.8 2.3 L5 5.6 L9.2 2.3" stroke="#2e2e30" stroke-width="0.9" fill="none"/></svg>
          liam@pimlu.com
        </li>
        <li>
          <svg viewBox="0 0 10 10"><circle cx="5" cy="5" r="4.5" fill="#e3141e"/><g stroke="#2e2e30" stroke-width="0.7" fill="none"><ellipse cx="5" cy="5" rx="1.8" ry="4.3"/><line x1="0.6" y1="5" x2="9.4" y2="5"/></g></svg>
          www.pimlu.com
        </li>
      </ul>
      <div class="rule"></div>
      <address class="address">PO Box 3190<br>Ashgrove Vale NSW 2760</address>
    </div>
    <div class="portrait" role="img" aria-label="Portrait photo of the agent in a dark suit"></div>
  </section>
</main>
</body>
</html>
```